Website for a company offering full serivce charging solutions for electric cars

The company "tanu-werk" (english: "tanu-works") offering all-in-one-solutions for charging infrastructure for electric mobility.

There are four products:
1- Wallboxes for single-family homes
2- Solutions for property devloper/-management for property parking space
3- All-in-one-charging solution for municipalities/communities
4- Solutions for tourism/hotels/holiday appartments

The Website structure:
1. Main Page
2.1. Product Page Single Homes
2.2. Product Page Property Management / Parking
2.3. Product Page Municipality
2.4. Product Page Tourism
3. Contact Form / Request for information
4. Imprint / Legal

The Website should be built on Wordpress with a powerful possibility to simply add/modify specific landing pages.

We would like you to implement the website later and also maintain it if possible, but we would be able to do minor modifications by ourselfs (for A/B-Testing)

The website should be clear and simple, easy to understand.
Target group is mainly B2C without deeper knowledge of that topic.

It should suggest, that we will provide a very simple way to get the charging infrastructure done.

We need a contact form, maybe we will use Hubspot later.

Attached you will find a draft of the main page and a landing page (for 2.2) - it is just the content, please ignore the design. We would love to let you create a suitable design.
Also you will find some drafts a bit different for the same story.

I added also a few stock photos, but they don't need to be used! If you have better ideas, you are welcome!

Industry/Entity Type

Charging/Electric mobility

Number of Pages Required

2 page

Font styles to use
Sans Serif

Requirements
Must have
• Based on Wordpress, and the designer should be able to implement it on Wordpress on a later step

```html
<!DOCTYPE html>
<html lang="de">
<head>
<meta charset="utf-8">
<title>tanu-werk – Ladelösungen</title>
<link rel="stylesheet" href="https://fonts.googleapis.com/css2?family=Titillium+Web:wght@400;600;700&family=Arimo:wght@400;500;600&display=swap">
<style>
:root{
  --navy:#121a2e;
  --navy-2:#152040;
  --navy-3:#0f1627;
  --pink:#e6178f;
  --purple:#7b4ad6;
  --white:#ffffff;
  --muted:#b9bfd0;
  --grid:#6a2a8a;
}
*{margin:0;padding:0;box-sizing:border-box}
html,body{width:1200px;height:4244px;overflow:hidden;background:var(--navy)}
body{position:relative;font-family:"Arimo",Arial,sans-serif;color:var(--white)}
.abs{position:absolute}
.head{font-family:"Titillium Web",Arial,sans-serif}
.btn{position:absolute;display:flex;align-items:center;justify-content:center;border-radius:30px;
  background:linear-gradient(90deg,var(--purple),var(--pink));font-family:"Titillium Web",Arial,sans-serif;
  font-weight:700;font-size:19px;color:var(--white);box-shadow:0 0 18px rgba(230,23,143,.45)}
.brand{display:flex;align-items:center;gap:10px}
.brand-dot{width:18px;height:18px;border-radius:50%;background:var(--pink)}
.brand-name{font-family:"Titillium Web",Arial,sans-serif;font-weight:600;color:var(--white)}

/* nav */
.site-nav{left:0;top:0;width:1200px;height:80px;background:var(--navy-3);border-bottom:3px solid #3b2a6a}
.nav-link{top:30px;font-size:16px;color:#e5e7ef}
.nav-link.active::after{content:"";position:absolute;left:0;right:0;bottom:-10px;height:2px;background:var(--pink)}
.tagline{font-size:13px;color:#cfd3de}

/* hero */
.hero{left:0;top:80px;width:1200px;height:597px;
  background:radial-gradient(circle at 78% 45%,#2d4fa8 0%,#1b2a55 25%,transparent 50%),
  linear-gradient(100deg,#1a2038 0%,#2a2f4a 45%,#3a3f5c 70%,#24366e 100%)}
.hero-title{left:110px;top:240px;font-size:56px;line-height:56px;color:var(--white)}
.hero-title b{font-weight:700}
.hero-title span{font-weight:400}
.hero-sub{left:110px;top:363px;font-size:20px;line-height:30px;color:#e9ebf2;width:470px}

/* intro */
.intro-mark{left:586px;top:748px;width:28px;height:28px;border-radius:50%;border:3px solid var(--pink)}
.intro-lead{left:200px;top:802px;width:800px;text-align:center;font-size:21px;line-height:33px;font-weight:500}
.intro-text{left:190px;top:920px;width:820px;text-align:center;font-size:15px;line-height:27.5px;color:var(--muted)}
.grid-band{left:0;width:1200px;background:linear-gradient(180deg,rgba(106,42,138,0) 0%,rgba(106,42,138,.35) 60%,rgba(106,42,138,.15) 100%)}

/* solutions */
.sol-title{left:0;top:1225px;width:1200px;text-align:center;font-size:38px;font-weight:400}
.card{top:1325px;width:306px;height:178px;border-radius:6px;
  background:linear-gradient(135deg,#1e2c52 0%,#2a3a66 55%,#1a2444 100%);display:flex;flex-direction:column;align-items:center;justify-content:center;gap:6px}
.card-dots{top:1390px;width:190px;height:125px;border-left:3px dotted var(--pink);border-bottom:3px dotted var(--pink)}
.card-label{font-family:"Titillium Web",Arial,sans-serif;font-weight:600;font-size:21px;line-height:21px;text-align:center}

/* product blocks */
.photo{border-radius:80px 0 80px 0}
.prod-title{font-size:38px;font-weight:600;color:var(--pink)}
.list{list-style:none;font-size:13.5px;line-height:17px;color:#e5e7ef}
.list li{position:relative;padding-left:20px;margin-bottom:8px}
.list li::before{content:"";position:absolute;left:2px;top:4px;width:6px;height:6px;border-right:2px solid var(--pink);border-top:2px solid var(--pink);transform:rotate(45deg)}
.list .sub{margin-left:14px;margin-bottom:3px}
.band-2{left:0;top:2134px;width:1200px;height:676px;background:linear-gradient(180deg,#142247 0%,#16244a 100%)}

/* contact */
.contact{left:0;top:3345px;width:1200px;height:536px;
  background:linear-gradient(100deg,#d81ea6 0%,#b82dc8 35%,#8a4ad8 62%,#4f5fd0 82%,#3a58c8 100%)}
.contact-photo{left:620px;top:3345px;width:580px;height:536px;
  background:radial-gradient(ellipse at 55% 70%,rgba(220,225,245,.45) 0%,rgba(150,160,230,.25) 30%,transparent 60%)}
.field{position:absolute;background:var(--white);font-size:12px;color:#6b6f7d;padding:14px 16px}
.submit{left:110px;top:3751px;width:176px;height:47px;border:2px solid var(--white);border-radius:25px;display:flex;align-items:center;justify-content:center;font-family:"Titillium Web",Arial,sans-serif;font-weight:700;font-size:17px}

/* footer */
.footer{left:0;top:3881px;width:1200px;height:297px;background:var(--navy-3)}
.f-div{top:3881px;width:1px;height:200px;background:#2a3148}
.f-head{top:3950px;font-family:"Titillium Web",Arial,sans-serif;font-weight:700;font-size:18px;padding-left:18px;border-left:3px solid var(--pink);line-height:22px}
.f-link{font-size:15px;color:#9aa0b4}
.social{top:3991px;width:33px;height:33px;border-radius:50%;background:var(--pink)}
.copy{left:0;top:4178px;width:1200px;height:66px;background:#1b2032;display:flex;align-items:center;justify-content:center;font-size:14px;color:#c6cad6}
</style>
</head>
<body>

<!-- navigation -->
<header class="abs site-nav">
  <div class="abs brand" style="left:102px;top:18px">
    <div class="brand-dot"></div>
    <div>
      <div class="brand-name" style="font-size:26px;line-height:26px">tanu-werk.de</div>
      <div class="tagline">einfach mehr als laden</div>
    </div>
  </div>
  <div class="abs nav-link active" style="left:456px">Lösungen</div>
  <div class="abs nav-link" style="left:585px">Unternehmen</div>
  <div class="abs nav-link" style="left:745px">Services</div>
  <div class="abs nav-link" style="left:864px">Karriere</div>
  <div class="btn" style="left:966px;top:23px;width:125px;height:40px;font-size:16px;font-weight:600">Kontakt</div>
</header>

<!-- hero -->
<section class="abs hero" role="img" aria-label="Ladestecker eines Elektroautos an einer Ladesäule bei Nacht"></section>
<h1 class="abs hero-title head"><b>TANU-WERK IST</b><br><span>IHR PARTNER</span></h1>
<p class="abs hero-sub">wenn das Laden nicht nur einfach, sondern die Umsetzung auch aus einer Hand kommen soll</p>
<div class="btn" style="left:110px;top:438px;width:174px;height:53px">KONTAKT</div>

<!-- intro -->
<div class="abs intro-mark"></div>
<p class="abs intro-lead">Wir&nbsp; bieten Lösungen sowohl für Privatkunden, Geschäftskunden als auch Kommunen an, die schnell, fair und ohne Eigenleistung zu einer smarten Ladelösung für E-Fahrzeuge kommen möchten.</p>
<p class="abs intro-text">Von der Beratung, über die Installation, Inbetriebnahme bis zur Abrechnung und Wartung bekommen Sie bei tanu-werk alles aus einer Hand. Auf Wunsch vermieten wir auch die Ladetechnik und übernehmen im gewerblichen Bereich die direkte Abrechnung mit dem Nutzer. Für Kommunen bieten wir den kostenfreien Full-Service an und beteiligen die Gemeinden an der Nutzung der Infrastruktur.</p>
<div class="abs grid-band" style="top:1038px;height:149px" role="img" aria-label="Leuchtendes Perspektivraster"></div>

<!-- solutions -->
<h2 class="abs sol-title head">Ladelösung für</h2>
<div class="abs card-dots" style="left:112px"></div>
<div class="abs card-dots" style="left:445px"></div>
<div class="abs card-dots" style="left:777px"></div>

<div class="abs card" style="left:124px" role="img" aria-label="Elektroauto vor einem Einfamilienhaus">
  <svg width="40" height="40" viewBox="0 0 40 40" fill="none" stroke="#fff" stroke-width="2"><path d="M5 20 20 6l15 14"/><path d="M9 17v18h22V17"/><rect x="17" y="25" width="6" height="10"/></svg>
  <div class="card-label">Single homes</div>
  <svg width="16" height="14" viewBox="0 0 16 14" fill="none" stroke="#fff" stroke-width="2"><path d="M3 1l5 5 5-5M3 7l5 5 5-5"/></svg>
</div>
<div class="abs card" style="left:457px" role="img" aria-label="Elektroauto in einer Wohnanlage">
  <svg width="44" height="42" viewBox="0 0 44 42" fill="none" stroke="#fff" stroke-width="2"><rect x="14" y="4" width="14" height="36"/><rect x="4" y="18" width="10" height="22"/><rect x="28" y="14" width="12" height="26"/><path d="M18 10h6M18 16h6M18 22h6M18 28h6M8 24h3M8 30h3M32 20h4M32 26h4"/></svg>
  <div class="card-label">Property management</div>
  <svg width="16" height="14" viewBox="0 0 16 14" fill="none" stroke="#fff" stroke-width="2"><path d="M3 1l5 5 5-5M3 7l5 5 5-5"/></svg>
</div>
<div class="abs card" style="left:789px" role="img" aria-label="Öffentliche Ladestation in einer Gemeinde">
  <svg width="48" height="48" viewBox="0 0 48 48" fill="none" stroke="#fff" stroke-width="2"><circle cx="24" cy="24" r="21" stroke-dasharray="10 4"/><circle cx="24" cy="18" r="4"/><circle cx="15" cy="24" r="3"/><circle cx="33" cy="24" r="3"/><path d="M17 34c0-5 3-8 7-8s7 3 7 8M10 33c0-3 2-5 5-5M38 33c0-3-2-5-5-5"/></svg>
  <div class="card-label">Communities/<br>municipalities</div>
  <svg width="16" height="14" viewBox="0 0 16 14" fill="none" stroke="#fff" stroke-width="2"><path d="M3 1l5 5 5-5M3 7l5 5 5-5"/></svg>
</div>

<!-- single homes -->
<div class="abs photo" style="left:107px;top:1635px;width:462px;height:359px;background:linear-gradient(120deg,#7c7262 0%,#b8ab95 45%,#d9d3c6 70%,#9b8f80 100%)" role="img" aria-label="Frau lädt ihr Elektroauto an der Wallbox zu Hause"></div>
<h2 class="abs prod-title head" style="left:595px;top:1630px">Eigenheimbesitzer</h2>
<ul class="abs list" style="left:595px;top:1710px;width:520px">
  <li>Bestandsanalyse mit umfangreicher Beratung über die Möglichkeiten der Umsetzung</li>
  <li>Prüfung und Übernahme der Anmeldung verfügbarer Fördermöglichkeiten</li>
  <li>Auswahl an smarten Wallbox Lösungen, passend für Ihr Fahrzeug und Ihre Bedürfnisse</li>
  <li>Installation inkl. aller notwendigen Materialien und Tätigkeiten (Durchbrüche, Erdarbeiten, etc.)</li>
  <li>Inbetriebnahme und Einweisung in die Ladetechnik</li>
  <li>Jährlich technische Wartung nach DGUV3</li>
</ul>
<div class="btn" style="left:595px;top:1928px;width:174px;height:53px">MEHR</div>

<!-- property management -->
<section class="abs band-2"></section>
<div class="abs grid-band" style="top:2637px;height:173px" role="img" aria-label="Leuchtendes Perspektivraster"></div>
<h2 class="abs prod-title head" style="left:0;top:2176px;width:1145px;text-align:center">Hausverwaltung / Bauträger</h2>
<ul class="abs list" style="left:130px;top:2295px;width:460px">
  <li>Durchführung einer individuellen Bedarfsanalyse inkl. Ermittlung der</li>
  <li>Anforderungen für:
    <div class="sub" style="margin-top:8px">› Haus- und Immobilienverwaltungen</div>
    <div class="sub">› Dienstleistungs- und Handelsunternehmen</div>
    <div class="sub">› Hotel und Beherbergungsbetriebe</div>
    <div class="sub">› Parkraum- und Parkhausbetreiber</div>
    <div class="sub">› Tourismus, Sport- und Freizeiteinrichtungen</div>
  </li>
  <li style="margin-top:22px">Planung und Projektierung des Installationsaufwands inkl.</li>
  <li style="margin-top:12px">Materialverbrauch</li>
  <li style="margin-top:12px">Leasing oder Kauf der Hardware</li>
</ul>
<div class="btn" style="left:124px;top:2563px;width:174px;height:53px">MEHR</div>
<ul class="abs list" style="left:626px;top:2284px;width:470px">
  <li style="margin-bottom:11px">Bei Bestandsbauten Integration der Ladeinfrastruktur in die</li>
  <li style="margin-bottom:11px">Gebäudesystemtechnik und ggf. Anpassung des Netzanschlusses</li>
  <li style="margin-bottom:11px">Inbetriebnahme der Anlage inkl. Prüf- und Messprotokollen</li>
  <li style="margin-bottom:11px">Wiederkehrende technische Prüfung der Anlage nach DGUV 3</li>
  <li>Austausch und Reparatur Service</li>
</ul>
<div class="abs photo" style="left:613px;top:2444px;width:430px;height:311px;border-radius:0 0 80px 0;background:linear-gradient(160deg,#6e6f73 0%,#3a3b40 45%,#1d1e22 70%,#55565a 100%)" role="img" aria-label="Dunkles Elektro-SUV in einer Tiefgarage"></div>

<!-- municipality -->
<div class="abs grid-band" style="top:3230px;height:115px" role="img" aria-label="Leuchtendes Perspektivraster"></div>
<div class="abs photo" style="left:137px;top:2930px;width:428px;height:312px;background:linear-gradient(120deg,#f1b660 0%,#c7834a 35%,#5d4a3c 65%,#c9c6c2 100%)" role="img" aria-label="Frau mit Smartphone neben ihrem ladenden Elektroauto bei Sonnenuntergang"></div>
<h2 class="abs prod-title head" style="left:623px;top:2925px">Kommune /Gemeinde</h2>
<ul class="abs list" style="left:623px;top:2992px;width:470px">
  <li style="margin-bottom:11px">Regelmäßige Wartung gemäß Vorschrift</li>
  <li style="margin-bottom:11px">Reparatur und Kundenservice</li>
  <li style="margin-bottom:11px">Direkte Abrechnung mit dem Nutzer</li>
  <li style="margin-bottom:11px">Beteiligung der Gemeinde am Umsatz</li>
  <li>Möglichkeit der Integration von Bonusprogrammen, mit denen der lokale Einzelhandel beworben wird</li>
</ul>
<div class="btn" style="left:613px;top:3174px;width:174px;height:53px">MEHR</div>

<!-- contact -->
<section class="abs contact"></section>
<div class="abs contact-photo" role="img" aria-label="Weißes Elektroauto lädt an einer Wandladestation"></div>
<h2 class="abs head" style="left:110px;top:3405px;font-size:38px;line-height:44px"><b style="font-weight:700">CONTACT</b> <span style="font-weight:400">US</span></h2>
<p class="abs" style="left:114px;top:3474px;width:470px;font-size:14px;line-height:17px">Lorem ipsum dolor sit amet, consectetur adipiscing elit, sed do eiusmod tempor incididunt ut labore et dolore magna aliqua.</p>
<div class="field" style="left:112px;top:3541px;width:238px;height:43px">First Name</div>
<div class="field" style="left:356px;top:3541px;width:238px;height:43px">Last Name</div>
<div class="field" style="left:112px;top:3594px;width:238px;height:43px">Email address</div>
<div class="field" style="left:356px;top:3594px;width:238px;height:43px">Phone number</div>
<div class="field" style="left:112px;top:3647px;width:482px;height:91px">Message</div>
<div class="abs submit">SUBMIT NOW</div>

<!-- footer -->
<footer class="abs footer"></footer>
<div class="abs brand" style="left:107px;top:3990px">
  <div class="brand-dot" style="width:26px;height:26px"></div>
  <div class="brand-name" style="font-size:36px;line-height:40px">tanu-werk.de</div>
</div>
<div class="abs f-div" style="left:391px"></div>
<div class="abs f-div" style="left:651px"></div>
<div class="abs f-div" style="left:865px"></div>
<div class="abs f-head" style="left:392px">NAVIGATION</div>
<div class="abs f-link" style="left:418px;top:3990px">AGB</div>
<div class="abs f-link" style="left:418px;top:4021px">Datenschutzerklärung</div>
<div class="abs f-link" style="left:418px;top:4052px">Impressum</div>
<div class="abs f-head" style="left:652px">RESOURCES</div>
<div class="abs f-link" style="left:674px;top:3990px">Kontakt</div>
<div class="abs f-link" style="left:674px;top:4021px">Karriere</div>
<div class="abs f-link" style="left:674px;top:4052px">FAQs</div>
<div class="abs f-head" style="left:867px">FOLLOW US</div>
<div class="abs social" style="left:884px"></div>
<div class="abs social" style="left:925px"></div>
<div class="abs social" style="left:965px"></div>
<div class="abs social" style="left:1006px"></div>
<div class="abs copy">© 2022 tanu-werk GmbH</div>

</body>
</html>
```